UK Online Auction Site needs a clever design

We need a contemporary landing page and registration page design for a UK auction website, that look equally at home on PC's and tablets . The design should be fresh, bright, clean, professional, robust, and familiar. We would like to see something clever but functional.

Online

```html
<!DOCTYPE html>
<html lang="en">
<head>
<meta charset="utf-8">
<title>Bidwell – UK Online Auctions</title>
<link href="https://fonts.googleapis.com/css2?family=Open+Sans:wght@300;400;600&display=swap" rel="stylesheet">
<style>
:root{
  --orange:#f26522;
  --header-top:#6a7490;
  --header-mid:#8a93ab;
  --page-top:#ececec;
  --page-bottom:#c9cacd;
  --card-border:#d6d6d6;
  --text-light:#ffffff;
  --text-muted:#555a66;
  --rule:#a8a9ad;
}
*{box-sizing:border-box;margin:0;padding:0}
html,body{width:814px;height:1200px;overflow:hidden}
body{
  position:relative;
  font-family:"Open Sans",Arial,sans-serif;
  background:linear-gradient(var(--page-top) 232px,#e6e6e7 600px,var(--page-bottom) 1200px);
}
.masthead{
  position:absolute;left:0;top:0;width:814px;height:232px;
  background:radial-gradient(ellipse 260px 180px at 407px 70px,#a9b1c4 0%,var(--header-mid) 45%,var(--header-top) 100%);
  border-bottom:1px solid #c2c4ca;
}
.welcome{position:absolute;left:124px;top:9px;font-size:7px;color:var(--orange)}
.welcome b{color:var(--text-light);font-weight:400}
.top-nav{position:absolute;left:446px;top:9px;display:flex;font-size:7px;color:var(--text-light)}
.top-nav span{margin-right:8px}
.account{position:absolute;left:600px;top:8px;display:flex;gap:18px;font-size:7px;color:var(--text-light);align-items:center}
.account svg{margin-right:4px;vertical-align:-1px}
.btn-register{position:absolute;left:577px;top:27px;width:47px;height:10px;background:#fff;font-size:5.5px;color:var(--text-muted);text-align:center;line-height:10px}
.or{position:absolute;left:631px;top:27px;font-size:6px;color:var(--text-light);line-height:10px}
.btn-login{position:absolute;left:644px;top:27px;width:46px;height:10px;background:var(--orange);font-size:5.5px;color:#fff;text-align:center;line-height:10px}
.brand{position:absolute;left:124px;top:40px;display:flex;align-items:center;gap:6px}
.brand-mark{width:14px;height:14px;background:var(--orange)}
.brand-name{font-size:22px;font-weight:600;color:var(--text-light);letter-spacing:.3px}
.search{position:absolute;left:284px;top:50px;width:406px;height:28px;background:var(--orange);font-size:6.5px;color:#fff}
.search .label{position:absolute;left:9px;top:9px}
.search .field{position:absolute;left:80px;top:6px;width:200px;height:14px;background:#fff;color:#888;padding-left:6px;line-height:14px}
.search .field i{position:absolute;right:3px;top:3px;width:8px;height:8px;border:1px solid #999}
.search .go{position:absolute;left:286px;top:6px;width:46px;height:14px;background:#fff;color:var(--text-muted);text-align:center;line-height:14px}
.search .adv{position:absolute;left:342px;top:9px;font-weight:600}
.categories{position:absolute;left:124px;top:116px;display:grid;grid-template-columns:274px 275px;column-gap:17px;row-gap:19px}
.card{height:230px;background:#fff;border:1px solid var(--card-border);display:flex;flex-direction:column}
.card-head{height:34px;border-bottom:1px solid #e4e4e4;display:flex;align-items:center;justify-content:space-between;padding:0 12px 0 13px}
.card-title{font-size:10.5px;font-weight:300;color:var(--orange)}
.partner{display:flex;align-items:center;gap:4px;font-size:6px;line-height:7px;color:#888}
.partner i{width:14px;height:14px;background:var(--orange);display:block}
.partner em{font-style:normal;font-weight:400;color:var(--orange)}
.card-body{flex:1;display:grid;grid-template-columns:1fr 64px;grid-template-rows:repeat(3,1fr);gap:2px 3px;padding:2px}
.card-body .hero{grid-row:1/4}
.footer{position:absolute;left:124px;top:1141px;width:566px;border-top:1px solid var(--rule);text-align:center;font-size:6.5px;color:var(--text-muted);padding-top:10px}
</style>
</head>
<body>
<header class="masthead">
  <p class="welcome">Welcome to <b>Bidwell !</b></p>
  <nav class="top-nav"><span>Sell</span><span>•</span><span>Help</span><span>•</span><span>Contact us</span></nav>
  <div class="account">
    <span><svg width="8" height="7" viewBox="0 0 8 7"><path d="M4 0v4M2 2.5L4 4.5 6 2.5M0.5 5v1.5h7V5" stroke="#fff" fill="none" stroke-width=".8"/></svg>Sign In</span>
    <span><svg width="8" height="7" viewBox="0 0 8 7"><path d="M0.5 2.5h7L6.5 6.5h-5zM2.5 2.5L4 0.5 5.5 2.5" stroke="#fff" fill="none" stroke-width=".8"/></svg>Basket</span>
  </div>
  <div class="btn-register">Register</div>
  <div class="or">or</div>
  <div class="btn-login">Login ▾</div>
  <div class="brand"><span class="brand-mark"></span><span class="brand-name">Bidwell</span></div>
  <form class="search">
    <span class="label">Search by Categories</span>
    <span class="field">e.g Pocket watch<i></i></span>
    <span class="go">Search</span>
    <span class="adv">Advanced Search</span>
  </form>
</header>

<main class="categories">
  <section class="card"><div class="card-head"><h2 class="card-title">Fashion</h2><div class="partner"><i></i><span>Created by<br><em>Harlowe</em></span></div></div>
    <div class="card-body">
      <div class="hero" role="img" aria-label="Three models in summer dresses" style="background:linear-gradient(90deg,#f4efe9,#d8cdbf 50%,#f2eeea)"></div>
      <div role="img" aria-label="Model in sunglasses" style="background:linear-gradient(#e9e4df,#8a6b55)"></div>
      <div role="img" aria-label="Model in floral dress" style="background:linear-gradient(#f1ebe4,#c89a72)"></div>
      <div role="img" aria-label="Model in patterned dress" style="background:linear-gradient(#f3efe9,#a38672)"></div>
    </div></section>
  <section class="card"><div class="card-head"><h2 class="card-title">Home &amp; Garden</h2><div class="partner"><i></i><span>Created by<br><em>Harlowe</em></span></div></div>
    <div class="card-body">
      <div class="hero" role="img" aria-label="Garden with wheelbarrow beside a green house wall" style="background:linear-gradient(#5f7a58,#4d6b3e 60%,#3f8a2e)"></div>
      <div role="img" aria-label="Suburban house" style="background:linear-gradient(#cfd8d6,#5e7a4a)"></div>
      <div role="img" aria-label="House with lawn" style="background:linear-gradient(#8da0a5,#3f6a36)"></div>
      <div role="img" aria-label="Flower garden" style="background:linear-gradient(#d9e2d6,#4e7a3a)"></div>
    </div></section>
  <section class="card"><div class="card-head"><h2 class="card-title">Electricals &amp; Technology</h2><div class="partner"><i></i><span>Created by<br><em>Harlowe</em></span></div></div>
    <div class="card-body">
      <div class="hero" role="img" aria-label="Close-up of a colourful circuit board" style="background:radial-gradient(circle at 45% 40%,#2f3a9a,#8a6a2a 55%,#c9b020)"></div>
      <div role="img" aria-label="Circuit board" style="background:linear-gradient(#3a5a7a,#1f3550)"></div>
      <div role="img" aria-label="Hand on a green board" style="background:linear-gradient(#b88060,#6a3a2a)"></div>
      <div role="img" aria-label="Pylons over a sunflower field" style="background:linear-gradient(#c9ccce,#d8a818)"></div>
    </div></section>
  <section class="card"><div class="card-head"><h2 class="card-title">Collectables &amp; Antiques</h2><div class="partner"><i></i><span>Created by<br><em>Harlowe</em></span></div></div>
    <div class="card-body">
      <div class="hero" role="img" aria-label="Antique furnished room" style="background:linear-gradient(#6a5c4e,#4a3a2a 60%,#2e2420)"></div>
      <div role="img" aria-label="Antique pocket watch" style="background:radial-gradient(circle,#e8d8a8,#6a5020)"></div>
      <div role="img" aria-label="Porcelain vases" style="background:linear-gradient(#6a7a6a,#b56a5a)"></div>
      <div role="img" aria-label="Vintage tin toy" style="background:linear-gradient(#f2f2f2,#8a8a72)"></div>
    </div></section>
  <section class="card"><div class="card-head"><h2 class="card-title">Jewellery &amp; Beauty</h2><div class="partner"><i></i><span>Created by<br><em>Harlowe</em></span></div></div>
    <div class="card-body">
      <div class="hero" role="img" aria-label="Diamond necklace and earrings" style="background:linear-gradient(#8a8a82,#c9b8a4 60%,#d8c8b4)"></div>
      <div role="img" aria-label="Gold ring" style="background:radial-gradient(circle,#c8a040,#111)"></div>
      <div role="img" aria-label="Earrings" style="background:linear-gradient(#4a5a6a,#2a3a4a)"></div>
      <div role="img" aria-label="Jewelled necklace" style="background:linear-gradient(#e6d2c8,#c8a090)"></div>
    </div></section>
  <section class="card"><div class="card-head"><h2 class="card-title">Toys</h2><div class="partner"><i></i><span>Created by<br><em>Harlowe</em></span></div></div>
    <div class="card-body">
      <div class="hero" role="img" aria-label="Teddy bear with letter blocks" style="background:radial-gradient(ellipse at 50% 45%,#a0602a,#e8dcd0 55%,#fff 75%)"></div>
      <div role="img" aria-label="Yellow plush bird" style="background:radial-gradient(circle,#f2d020,#fff 70%)"></div>
      <div role="img" aria-label="Toy drum" style="background:radial-gradient(circle,#d8a870,#fff 70%)"></div>
      <div role="img" aria-label="Toy fire truck" style="background:radial-gradient(circle,#c82020,#fff 70%)"></div>
    </div></section>
  <section class="card"><div class="card-head"><h2 class="card-title">Sport &amp; Leisure</h2><div class="partner"><i></i><span>Created by<br><em>Harlowe</em></span></div></div>
    <div class="card-body">
      <div class="hero" role="img" aria-label="Assorted sports balls" style="background:radial-gradient(ellipse at 50% 50%,#c87a3a,#e8dcd0 45%,#fff 70%)"></div>
      <div role="img" aria-label="Bowling balls and pins" style="background:linear-gradient(#3a5a7a,#8a5a3a)"></div>
      <div role="img" aria-label="Gym training" style="background:linear-gradient(#d0d6da,#3a4a6a)"></div>
      <div role="img" aria-label="Basketball player" style="background:linear-gradient(#fff,#c89070)"></div>
    </div></section>
  <section class="card"><div class="card-head"><h2 class="card-title">Motors</h2><div class="partner"><i></i><span>Created by<br><em>Harlowe</em></span></div></div>
    <div class="card-body">
      <div class="hero" role="img" aria-label="Red sports motorbike" style="background:radial-gradient(ellipse at 55% 45%,#c81818,#3a0808 55%,#050505)"></div>
      <div role="img" aria-label="Engine" style="background:linear-gradient(#7a7a7a,#1a1a1a)"></div>
      <div role="img" aria-label="Red SUV" style="background:radial-gradient(circle,#8a1a1a,#fff 70%)"></div>
      <div role="img" aria-label="Engine components" style="background:linear-gradient(#b8bcc0,#a05a3a)"></div>
    </div></section>
</main>

<footer class="footer">Copyright © 2014 Bidwell. All Rights Reserved</footer>
</body>
</html>
```